Business Cards Design for the electrical wholesaler: clean bold dynamic :)

We need a business card design that would follow our latest brand guidelines. As an electrical wholesaler we want to bring a fresh look and feel into the industry. The design should be clean bold and dynamic. It should come alive with the renewed energy of our green colour. Our grey colour should keep things balanced and complement the notion of maturity and responsibility. We employ Lato as a corporate font however are not bound by this font and we’re open to interpretation here.

Target Market(s)

Electrical contractors

Industry/Entity Type

Business

Contact Information for Business Card

Logo
Name & Surname: Halyna Dorosh
Job Title: Director of Marketing
Email: halya.dorosh@quillmail.example
Cell phone: XXX.XXX.XXXX
Address: 20517 - 87 Ave. Edmonton, AB, Canada. T6K 4N8
Business Phone: 780.555.0184
Website: www.brovix.example

Font styles to use
Other font styles liked:
• Lato

Requirements
Must have
• Logo & website
Nice to have
• Brand elements - some of them you may find in the attached Brand Guidelines (e.g. three lines on the background signifying "W")

```html
<!DOCTYPE html>
<html lang="en">
<head>
<meta charset="utf-8">
<title>Brovix Electrical Wholesalers – Business Card</title>
<link rel="stylesheet" href="https://fonts.googleapis.com/css2?family=Lato:wght@300;400;700;900&display=swap">
<style>
  :root {
    --green: #8cc63f;
    --green-light: #a5d468;
    --grey-dark: #3c3c3e;
    --charcoal: #262628;
    --white: #ffffff;
    --mist: #ececec;
    --backdrop: #2e2e30;
  }
  * { margin: 0; padding: 0; box-sizing: border-box; }
  html, body { width: 1200px; height: 799px; overflow: hidden; }
  body {
    background: var(--backdrop);
    font-family: "Lato", sans-serif;
    position: relative;
  }
  .card {
    position: absolute;
    width: 620px;
    height: 354px;
    overflow: hidden;
    box-shadow: 0 10px 24px rgba(0,0,0,.45);
  }
  .card--front { left: 290px; top: 28px; background: var(--green); }
  .card--back  { left: 290px; top: 416px; background: var(--mist); }
  .card svg.shapes { position: absolute; inset: 0; }

  .city-tint {
    position: absolute; inset: 0;
  }
  .card--front .city-tint {
    background: linear-gradient(180deg, rgba(255,255,255,.10), rgba(255,255,255,0) 70%);
  }
  .card--back .city-tint {
    background: linear-gradient(160deg, #f4f4f4 0%, #dadada 55%, #cfcfcf 100%);
  }

  .wordmark {
    position: absolute;
    display: flex;
    align-items: center;
    gap: 12px;
  }
  .wordmark__dot {
    width: 40px; height: 40px; border-radius: 50%;
  }
  .wordmark__name {
    font-weight: 700;
    font-size: 64px;
    line-height: 1;
    letter-spacing: -1px;
  }
  .wordmark__tag {
    font-weight: 700;
    font-size: 11px;
    letter-spacing: 1.6px;
    margin-top: 2px;
  }
  .card--front .wordmark { left: 150px; top: 120px; }
  .card--front .wordmark__dot { background: var(--white); }
  .card--front .wordmark__name { color: var(--grey-dark); }
  .card--front .wordmark__tag { color: var(--grey-dark); }

  .site-url {
    position: absolute; left: 0; right: 0; top: 300px;
    text-align: center;
    color: var(--white);
    font-weight: 700;
    font-size: 12px;
    letter-spacing: 5px;
  }

  .card--back .wordmark { left: 40px; top: 236px; }
  .card--back .wordmark__dot { background: var(--green); width: 32px; height: 32px; }
  .card--back .wordmark__name { color: var(--grey-dark); font-size: 52px; }
  .card--back .wordmark__tag { color: var(--grey-dark); font-size: 9px; }

  .contact {
    position: absolute; left: 418px; top: 62px; width: 190px;
    color: var(--white);
  }
  .contact__name { font-size: 24px; font-weight: 400; line-height: 1.1; }
  .contact__name strong { font-weight: 900; color: var(--grey-dark); }
  .contact__rule { height: 1px; background: var(--white); margin: 8px 0 6px; }
  .contact__title { font-size: 11px; color: var(--grey-dark); font-weight: 400; }
  .contact__list { list-style: none; margin-top: 18px; }
  .contact__item {
    display: flex; align-items: center; gap: 10px;
    font-size: 11px; line-height: 1.35; margin-bottom: 12px;
  }
  .contact__icon {
    flex: none; width: 20px; height: 20px; border-radius: 4px;
    background: var(--white);
    display: flex; align-items: center; justify-content: center;
  }
</style>
</head>
<body>

<section class="card card--front" aria-label="Business card front">
  <div class="city-tint" role="img" aria-label="Faint city skyline photograph in green tones"></div>
  <svg class="shapes" width="620" height="354" viewBox="0 0 620 354" aria-hidden="true">
    <polygon points="70,0 190,0 160,40 100,40" fill="var(--white)"/>
    <polygon points="500,0 620,0 620,120 560,60" fill="var(--charcoal)"/>
    <polygon points="0,230 60,290 120,354 0,354" fill="var(--charcoal)"/>
  </svg>
  <div class="wordmark">
    <span class="wordmark__dot"></span>
    <div>
      <div class="wordmark__name">brovix</div>
      <div class="wordmark__tag">ELECTRICAL WHOLESALERS</div>
    </div>
  </div>
  <div class="site-url">WWW.BROVIX.EXAMPLE</div>
</section>

<section class="card card--back" aria-label="Business card back">
  <div class="city-tint" role="img" aria-label="Faint grey city skyline photograph"></div>
  <svg class="shapes" width="620" height="354" viewBox="0 0 620 354" aria-hidden="true">
    <polygon points="330,0 620,0 620,354 370,354 400,175" fill="var(--green)"/>
    <polygon points="370,354 620,354 620,230" fill="var(--green-light)" opacity=".7"/>
    <polygon points="530,0 620,0 620,100" fill="var(--charcoal)"/>
  </svg>
  <div class="wordmark">
    <span class="wordmark__dot"></span>
    <div>
      <div class="wordmark__name">brovix</div>
      <div class="wordmark__tag">ELECTRICAL WHOLESALERS</div>
    </div>
  </div>
  <div class="contact">
    <div class="contact__name"><strong>Halyna</strong> Dorosh</div>
    <div class="contact__rule"></div>
    <div class="contact__title">Director of Marketing</div>
    <ul class="contact__list">
      <li class="contact__item">
        <span class="contact__icon">
          <svg width="12" height="12" viewBox="0 0 12 12" aria-hidden="true"><rect x="3" y="0.5" width="6" height="11" rx="1.2" fill="none" stroke="var(--charcoal)" stroke-width="1.3"/><circle cx="6" cy="9.5" r=".8" fill="var(--charcoal)"/></svg>
        </span>
        <span>+1 555 010 7788<br>780.555.0184</span>
      </li>
      <li class="contact__item">
        <span class="contact__icon">
          <svg width="12" height="12" viewBox="0 0 12 12" aria-hidden="true"><circle cx="6" cy="6" r="5" fill="none" stroke="var(--charcoal)" stroke-width="1.3"/><path d="M1 6h10M6 1c2 2.5 2 7.5 0 10M6 1c-2 2.5-2 7.5 0 10" fill="none" stroke="var(--charcoal)" stroke-width="1"/></svg>
        </span>
        <span>halya.dorosh@quillmail.example<br>www.brovix.example</span>
      </li>
      <li class="contact__item">
        <span class="contact__icon">
          <svg width="12" height="12" viewBox="0 0 12 12" aria-hidden="true"><path d="M6 11.5C3.5 8 2.5 6.3 2.5 4.5a3.5 3.5 0 0 1 7 0c0 1.8-1 3.5-3.5 7z" fill="var(--charcoal)"/><circle cx="6" cy="4.5" r="1.2" fill="var(--white)"/></svg>
        </span>
        <span>20517 - 87 Ave. Edmonton,<br>AB, Canada. T6K 4N8</span>
      </li>
    </ul>
  </div>
</section>

</body>
</html>
```